Business software developers new website

We need to redesign our website. Our current website is http://www.plovencast.example/index.html, which is outdated and needs a new look. We moved out from web design and have concentrated more on the back end of the systems, for example, system support and security and cloud-based applications. Our major clients include both private and government sectors. We would like to see some designs that are all in one page, simple and clean. Prefer illustrator or obstructed images instead of real-life photos. Must look futuristic yet friendly. Attached the new logo for your references and good luck.

Target Market(s)

Medium to big company for their IT or data management. Either improve or upgrade their current system.

Industry/Entity Type

Business Software

Number of Pages Required

1 page

Colors

Designer to choose colors to be used in the design.

Requirements
Must have
• Simple and clean. Individual assets must be provided in the correct size and format(png or jpeg). Prefer Goggle fonts. Even though the logo color is red, grey and black, still prefer some modern colors that go well with red. When design, must consider the possibility to convert it into responsive.
Nice to have
• White background
Should not have
• real life photos, no slider

```html
<!DOCTYPE html>
<html lang="en">
<head>
<meta charset="utf-8">
<title>plovencast.net — Software and Web Development</title>
<link rel="stylesheet" href="https://fonts.googleapis.com/css2?family=Montserrat:wght@400;500;600;700&family=Open+Sans:wght@400;600&display=swap">
<style>
:root{
  --red:#e52a37;
  --pink:#fbdde0;
  --ink:#1d1d1f;
  --text:#555a60;
  --muted:#8a8f95;
  --grey-band:#efefef;
  --white:#ffffff;
  --line:#e3e3e3;
  --lilac:#ece9f4;
  --lilac-dark:#d8d3e8;
}
*{box-sizing:border-box;margin:0;padding:0}
html,body{width:1200px;height:2660px;overflow:hidden;background:var(--white)}
body{font-family:"Open Sans",Arial,sans-serif;color:var(--text);position:relative}
.heading{font-family:"Montserrat",Arial,sans-serif}
.btn{display:inline-block;background:var(--red);color:var(--white);font-family:"Montserrat",Arial,sans-serif;font-weight:600;font-size:15px;border-radius:22px;padding:12px 30px;white-space:nowrap}
.wordmark{font-family:"Montserrat",Arial,sans-serif;font-weight:600;color:var(--ink);white-space:nowrap}

/* header */
.site-header{position:absolute;top:0;left:0;width:1200px;height:120px}
.site-header .wordmark{position:absolute;left:110px;top:40px;font-size:36px}
.phone-btn{position:absolute;right:110px;top:14px;background:var(--red);color:var(--white);font-family:"Montserrat",Arial,sans-serif;font-size:14px;font-weight:600;padding:10px 22px;border-radius:20px;display:flex;align-items:center;gap:8px}
.main-nav{position:absolute;right:110px;top:70px;display:flex;gap:54px;font-family:"Montserrat",Arial,sans-serif;font-size:16px;font-weight:500;color:var(--ink)}

/* hero */
.hero-blob{position:absolute;left:0;top:580px}
.hero-art{position:absolute;left:560px;top:110px;width:520px;height:520px}
.hero-copy{position:absolute;left:110px;top:240px;width:440px}
.hero-copy h1{font-size:64px;font-weight:700;color:var(--red);letter-spacing:-1px;margin-bottom:18px}
.hero-copy p{font-size:15px;line-height:1.6;margin-bottom:36px}

/* company */
.company{position:absolute;left:170px;top:790px;width:860px;height:500px;background:var(--white);box-shadow:0 10px 40px rgba(0,0,0,.12);text-align:center;padding:70px 90px}
.section-title{font-family:"Montserrat",Arial,sans-serif;font-size:46px;font-weight:600;color:var(--ink);text-align:center}
.section-title span{color:var(--red)}
.company p{font-size:15px;line-height:1.75;margin:26px 0 30px}

/* services */
.services{position:absolute;left:0;top:1380px;width:1200px;height:530px;background:var(--grey-band)}
.services .section-title{margin-top:110px}
.service-list{position:absolute;left:120px;top:208px;width:960px;display:flex;justify-content:space-between}
.service{width:210px}
.service svg{display:block;margin-bottom:12px}
.service h3{font-family:"Montserrat",Arial,sans-serif;font-size:16px;font-weight:600;color:var(--ink);margin-bottom:6px;white-space:nowrap}
.service.active h3{color:var(--red)}
.service p{font-size:13px;line-height:1.55;color:var(--muted)}
.services .btn{position:absolute;left:540px;top:460px}

/* clients */
.clients{position:absolute;left:0;top:1910px;width:1200px;height:400px}
.clients .section-title{margin-top:80px}
.client-row{position:absolute;left:270px;top:212px;width:660px;display:flex;justify-content:space-between}
.client{width:190px;height:110px;background:var(--white);box-shadow:0 4px 16px rgba(0,0,0,.1);display:flex;align-items:center;justify-content:center;gap:8px;font-family:"Montserrat",Arial,sans-serif;font-size:20px;font-weight:600;color:var(--ink)}
.client .mark{width:14px;height:14px;background:var(--red)}
.arrow{position:absolute;top:243px;width:48px;height:48px;border-radius:50%;background:var(--red);display:flex;align-items:center;justify-content:center}
.arrow.prev{left:120px}.arrow.next{right:120px}

/* newsletter */
.newsletter{position:absolute;left:0;top:2310px;width:1200px;height:270px;background:var(--grey-band)}
.newsletter .section-title{margin-top:50px;font-size:42px}
.subscribe{position:absolute;left:225px;top:150px;display:flex;gap:20px}
.subscribe .field{width:430px;height:40px;background:var(--white);border:1px solid var(--line);display:flex;align-items:center;justify-content:space-between;padding:0 14px;font-size:13px;color:var(--muted)}
.subscribe .submit{width:180px;height:40px;background:var(--red);color:var(--white);font-family:"Montserrat",Arial,sans-serif;font-weight:600;font-size:15px;display:flex;align-items:center;justify-content:center}

/* footer */
.site-footer{position:absolute;left:0;top:2580px;width:1200px;height:80px}
.site-footer .wordmark{position:absolute;left:110px;top:20px;font-size:28px}
.site-footer .main-nav{top:16px;font-size:14px;gap:44px}
.copyright{position:absolute;right:110px;top:48px;font-size:12px;color:var(--muted)}
</style>
</head>
<body>

<header class="site-header">
  <div class="wordmark">plovencast.net</div>
  <div class="phone-btn">
    <svg width="14" height="14" viewBox="0 0 24 24" fill="#fff"><path d="M6.6 10.8a15 15 0 0 0 6.6 6.6l2.2-2.2a1 1 0 0 1 1-.25 11.4 11.4 0 0 0 3.6.57 1 1 0 0 1 1 1V20a1 1 0 0 1-1 1A17 17 0 0 1 3 4a1 1 0 0 1 1-1h3.5a1 1 0 0 1 1 1c0 1.25.2 2.45.57 3.6a1 1 0 0 1-.25 1z"/></svg>
    +61 7 5550 0142
  </div>
  <nav class="main-nav"><span>Home</span><span>Our Services</span><span>Our Clients</span><span>Contacts</span></nav>
</header>

<svg class="hero-blob" width="560" height="340" viewBox="0 0 560 340" aria-hidden="true">
  <path d="M0 40 C120 0 260 20 360 70 C470 125 540 180 500 250 C460 320 300 300 180 320 C100 334 40 330 0 320 Z" fill="var(--pink)"/>
</svg>

<div class="hero-art" role="img" aria-label="Illustration of two people working at computer desks in an office">
  <svg width="520" height="520" viewBox="0 0 520 520">
    <path d="M80 90 C170 10 360 0 450 80 C530 150 500 270 470 360 C430 470 320 520 210 490 C100 460 40 380 40 280 C40 200 30 140 80 90 Z" fill="var(--lilac)"/>
    <rect x="120" y="300" width="300" height="60" rx="8" fill="var(--lilac-dark)"/>
  </svg>
</div>

<section class="hero-copy">
  <h1 class="heading">plovencast</h1>
  <p>Plovencast.net is an Australian based Software and Web Development Company that provides individual technology solutions and professional software for clients worldwide.</p>
  <span class="btn">Learn More</span>
</section>

<section class="company">
  <h2 class="section-title">Our <span>Company</span></h2>
  <p>Plovencast.net is an Australian based Software and Web Development Company that provides individual technology solutions and professional software for clients worldwide. Our work is based on quality sales, customer and technical support services. Being oriented towards innovative productivity in our work, we come up with essential tools for online business enhancing. Our programming specialists focus on delivering solutions for small start-ups as well as large organizations and companies. The team of purposeful and experienced professionals works hard to extract maximum performance from modern information technologies.</p>
  <span class="btn">Learn More</span>
</section>

<section class="services">
  <h2 class="section-title">Our <span>Services</span></h2>
  <div class="service-list">
    <div class="service">
      <svg width="44" height="44" viewBox="0 0 44 44" fill="none" stroke="var(--ink)" stroke-width="2"><path d="M6 36h32M10 36l4-14h16l4 14M18 22V10M26 22V6M22 22V12"/></svg>
      <h3>Web Design</h3>
      <p>Your website needs the 'wow' factor to meet your audience needs.</p>
    </div>
    <div class="service active">
      <svg width="44" height="44" viewBox="0 0 44 44" fill="none" stroke="var(--red)" stroke-width="2"><rect x="4" y="7" width="36" height="24" rx="2"/><path d="M16 38h12M22 31v7M17 15l-4 4 4 4M27 15l4 4-4 4"/></svg>
      <h3>Software Development</h3>
      <p>We build robust, reliable websites – and make sure they stay that way.</p>
    </div>
    <div class="service">
      <svg width="44" height="44" viewBox="0 0 44 44" fill="none" stroke="var(--ink)" stroke-width="2"><path d="M6 18v8h6l14 8V10L12 18z M32 16c3 2 3 10 0 12M14 26l3 10h4l-2-9"/></svg>
      <h3>Marketing</h3>
      <p>Results using the latest techniques to improve your Search Engine Ranking.</p>
    </div>
    <div class="service">
      <svg width="44" height="44" viewBox="0 0 44 44" fill="none" stroke="var(--ink)" stroke-width="2"><circle cx="22" cy="22" r="7"/><path d="M22 5v6M22 33v6M5 22h6M33 22h6M10 10l4 4M30 30l4 4M34 10l-4 4M14 30l-4 4"/></svg>
      <h3>Programming</h3>
      <p>We specialize in a variety of programming languages, but primarily use the following</p>
    </div>
  </div>
  <span class="btn">View More</span>
</section>

<section class="clients">
  <h2 class="section-title">Our <span>Clients</span></h2>
  <div class="arrow prev"><svg width="16" height="16" viewBox="0 0 16 16"><path d="M10 3L5 8l5 5" stroke="#fff" stroke-width="2.5" fill="none"/></svg></div>
  <div class="client-row">
    <div class="client"><span class="mark"></span>Brightlane</div>
    <div class="client"><span class="mark"></span>Norvale</div>
    <div class="client">Corelli's</div>
  </div>
  <div class="arrow next"><svg width="16" height="16" viewBox="0 0 16 16"><path d="M6 3l5 5-5 5" stroke="#fff" stroke-width="2.5" fill="none"/></svg></div>
</section>

<section class="newsletter">
  <h2 class="section-title">Newsletter <span>Subscribe</span></h2>
  <div class="subscribe">
    <div class="field">Enter email id
      <svg width="16" height="12" viewBox="0 0 16 12" fill="none" stroke="var(--red)" stroke-width="1.5"><rect x="1" y="1" width="14" height="10"/><path d="M1 1l7 6 7-6"/></svg>
    </div>
    <div class="submit">Subscribe</div>
  </div>
</section>

<footer class="site-footer">
  <div class="wordmark">plovencast.net</div>
  <nav class="main-nav"><span>Home</span><span>Our Services</span><span>Our Clients</span><span>Contacts</span></nav>
  <div class="copyright">© Copyrights 2019 &nbsp;|&nbsp; All Rights Reserved</div>
</footer>

</body>
</html>
```